Social Media App Needs PPT Template

We need a PowerPoint template for a new social media company based in the DC area called "Bold Ledger." We provide an interactive digital platform for executives to share actionable advice. We would like to see designs that use our orange logo color as an accent, but are mainly grey, white, and black. The final design should communicate clean, chic, modern, and professional.

Target Market(s)

Executives

Industry/Entity Type

Information Technology

Font styles to use
Sans Serif

Colors
f78f20
fbe7d2
ffffff
000000
e8e8e8
757575

Requirements
Must have
• My project must have title page and many options for the body of the ppt (graphs, tables, etc). It also needs to be easy to modify. I must have someone who is experienced in creating powerpoint templates.
Nice to have
• It would be nice to have a very modern and clean design that includes the logo on every page, but still leaves a lot of room for the content of the slide
Should not have
• My design project should not look to busy.

```html
<!DOCTYPE html>
<html lang="en">
<head>
<meta charset="utf-8">
<title>About Our Company – Bold Ledger</title>
<link href="https://fonts.googleapis.com/css2?family=Lato:wght@300;400;700;900&display=swap" rel="stylesheet">
<style>
  :root {
    --stage: #555555;
    --paper: #f7f7f7;
    --orange: #e8871e;
    --orange-light: #f0962a;
    --navy: #232c3b;
    --ink: #2c2c2c;
    --white: #ffffff;
    --footer-text: #c9ccd2;
  }
  * { margin: 0; padding: 0; box-sizing: border-box; }
  html, body {
    width: 1200px; height: 960px; overflow: hidden;
    background: var(--stage);
    font-family: "Lato", sans-serif;
  }
  .page-label {
    position: absolute; top: 74px; left: 0; width: 1200px;
    text-align: center; color: var(--white);
    font-weight: 300; font-size: 29px; letter-spacing: 0.5px;
  }
  .slide {
    position: absolute; left: 111px; top: 135px;
    width: 970px; height: 727px;
    background: radial-gradient(ellipse at 50% 40%, #ffffff 0%, var(--paper) 70%, #efefef 100%);
    overflow: hidden;
  }
  .slide-bands { position: absolute; left: 0; top: 0; }
  .slide-title {
    position: absolute; left: 30px; top: 60px;
    color: var(--white); font-weight: 300; font-size: 38px; line-height: 1;
  }
  .brand {
    position: absolute; right: 34px; top: 70px;
    color: var(--white); font-weight: 700; font-size: 25px; line-height: 1;
    display: flex; align-items: center; gap: 10px;
  }
  .brand-dot { width: 14px; height: 14px; border-radius: 50%; background: var(--orange); }
  .features {
    position: absolute; left: 45px; top: 0; width: 880px; height: 727px;
  }
  .feature { position: absolute; top: 210px; width: 254px; }
  .feature-icon { display: block; margin: 0 auto; height: 110px; }
  .feature-text {
    margin-top: 43px;
    font-size: 17px; line-height: 24.8px; color: var(--ink);
    text-align: justify; text-align-last: center; hyphens: auto;
  }
  .feature--growth { left: 0; }
  .feature--partnership { left: 314px; }
  .feature--approval { left: 624px; }
  .slide-footer-text {
    position: absolute; left: 26px; top: 694px;
    font-size: 13px; color: var(--footer-text); line-height: 18px;
  }
  .slide-footer-text .sep { margin: 0 6px; }
</style>
</head>
<body>
  <div class="page-label">Page 5</div>

  <section class="slide">
    <svg class="slide-bands" width="970" height="727" viewBox="0 0 970 727" aria-hidden="true">
      <polygon points="761,33 970,33 970,42 752,42" fill="var(--orange)"/>
      <polygon points="0,46 737,46 661,122 0,122" fill="var(--orange)"/>
      <polygon points="560,46 737,46 700,83 520,83" fill="var(--orange-light)" opacity="0.45"/>
      <polygon points="744,46 970,46 970,122 668,122" fill="var(--navy)"/>
      <polygon points="0,125 651,125 643,135 0,135" fill="var(--navy)"/>
      <polygon points="0,689 277,689 247,717 0,717" fill="var(--navy)"/>
      <polygon points="282,689 970,689 970,717 253,717" fill="var(--orange)"/>
    </svg>

    <h1 class="slide-title">About Our Company</h1>
    <div class="brand"><span class="brand-dot"></span>Bold Ledger</div>

    <div class="features">
      <article class="feature feature--growth">
        <svg class="feature-icon" width="140" height="110" viewBox="0 0 140 110" aria-hidden="true">
          <g fill="none" stroke="var(--navy)" stroke-width="5" stroke-linejoin="round" stroke-linecap="round">
            <rect x="7" y="5" width="126" height="90"/>
            <rect x="18" y="14" width="104" height="70"/>
            <rect x="2" y="95" width="136" height="10"/>
            <polyline points="36,58 55,45 70,55 94,34"/>
          </g>
        </svg>
        <p class="feature-text">Duis autem vel eum iriure dolor in hendrerit in vulputate velit esse molestie consequat, vel illum dolore eu feugiat nulla facilisis at vero eros et accumsan et iusto odio dignissim qui blan-dit praesent luptatum zzril del enit augue duis dolore te feugait nulla facilisi.</p>
      </article>

      <article class="feature feature--partnership">
        <svg class="feature-icon" width="140" height="110" viewBox="0 0 140 110" aria-hidden="true">
          <g fill="none" stroke="var(--orange)" stroke-width="5" stroke-linejoin="round" stroke-linecap="round">
            <polygon points="3,30 20,10 32,20 15,42"/>
            <polygon points="137,30 120,10 108,20 125,42"/>
            <path d="M32,22 L48,28 L62,22 L80,22 L108,22"/>
            <path d="M62,22 L48,40 C54,46 62,42 70,34 L96,58"/>
            <path d="M108,22 L122,42 L100,78"/>
            <path d="M17,42 L32,64"/>
            <circle cx="38" cy="68" r="6"/>
            <circle cx="48" cy="77" r="6"/>
            <circle cx="58" cy="85" r="6"/>
            <circle cx="69" cy="92" r="6"/>
            <path d="M74,94 L82,98 C88,100 92,92 86,88 M86,88 L94,90 C100,90 100,82 94,78 M94,78 L100,78 C106,76 104,66 96,64"/>
          </g>
        </svg>
        <p class="feature-text">Duis autem vel eum iriure dolor in hendrerit in vulputate velit esse molestie consequat, vel illum dolore eu feugiat nulla facilisis at vero eros et accumsan et iusto odio dignissim qui blan-dit praesent luptatum zzril dele nit augue duis dolore te feugait nulla facilisi.</p>
      </article>

      <article class="feature feature--approval">
        <svg class="feature-icon" width="140" height="110" viewBox="0 0 140 110" aria-hidden="true">
          <g fill="none" stroke="var(--navy)" stroke-width="5" stroke-linejoin="round" stroke-linecap="round">
            <rect x="22" y="44" width="16" height="42"/>
            <rect x="38" y="40" width="14" height="50"/>
            <path d="M52,44 L62,40 L80,18 L82,4 C92,2 96,12 92,24 L88,38 L108,38 C116,38 118,48 110,50 C118,52 118,62 110,64 C118,66 116,76 108,76 C114,80 112,90 104,90 L58,90 L52,86"/>
            <line x1="45" y1="52" x2="45" y2="53"/>
          </g>
        </svg>
        <p class="feature-text">Duis autem vel eum iriure dolor in hendrerit in vulputate velit esse molestie consequat, vel illum dolore eu feugiat nulla facilisis at vero eros et accumsan et iusto odio dignissim qui blan-dit praesent luptatum zzril del enit augue duis dolore te feugait nulla facilisi.</p>
      </article>
    </div>

    <div class="slide-footer-text">www.boldledger.com<span class="sep">|</span>Page 3</div>
  </section>
</body>
</html>
```